Simple Recipe eBook

I need the graphic work done for a simple recipe ebook, I have attached all of the required information for it, as well as our company logo. Further company info can be found at velorabix.com

I would like each recipe page to include 2 recipes, each recipe needs to include ingredients, picture, method, and nutritional info.

I would like the style to appear fresh and healthy, with lots of graphics and colours to match.
Please let me know if you need any guidance

Target Market(s)

Females aged from 15-25

Industry/Entity Type

It Company

```html
<!DOCTYPE html>
<html lang="en">
<head>
<meta charset="utf-8">
<title>Velorabix Recipe Guide – Intro Page</title>
<link rel="stylesheet" href="https://fonts.googleapis.com/css2?family=Bree+Serif&family=Pacifico&display=swap">
<style>
  :root {
    --canvas: #ffffff;
    --page-yellow: #f8d35f;
    --pattern-yellow: #f1c956;
    --ink: #1e1a14;
    --script-grey: #4d4a4b;
    --logo-grey: #4a4648;
    --plate-tone: #c9a94a;
  }
  * { margin: 0; padding: 0; box-sizing: border-box; }
  html, body {
    width: 1200px; height: 1000px; overflow: hidden;
    background: var(--canvas);
  }
  .canvas { position: relative; width: 1200px; height: 1000px; }
  .page {
    position: absolute; left: 250px; top: 26px;
    width: 708px; height: 943px;
    background: var(--page-yellow);
    overflow: hidden;
  }
  .pattern-band {
    position: absolute;
    background: linear-gradient(180deg, var(--pattern-yellow), #f3cc5a);
  }
  .pattern-band--top { left: 0; top: 0; width: 708px; height: 69px; }
  .pattern-band--bottom { left: 0; top: 880px; width: 708px; height: 63px; }
  .footer-arch {
    position: absolute; left: 112px; top: 836px;
    width: 484px; height: 300px;
    background: var(--canvas);
    border-radius: 50%;
  }
  .table-setting {
    position: absolute; left: 230px; top: 187px;
    width: 272px; height: 178px;
    background: radial-gradient(ellipse at 45% 45%, #f4f1ea 0 28%, #e6c658 52%, var(--page-yellow) 72%);
    border-radius: 40px;
  }
  .intro {
    position: absolute; left: 0; top: 377px; width: 708px;
    text-align: center;
    font-family: "Bree Serif", serif;
    font-size: 13.5px; line-height: 21px;
    color: var(--ink);
  }
  .intro p + p { margin-top: 19px; }
  .countdown {
    position: absolute; left: 0; top: 548px; width: 708px;
    text-align: center;
    font-family: "Pacifico", cursive;
    font-size: 31px; color: var(--script-grey);
  }
  .countdown span { display: block; height: 66px; line-height: 50px; }
  .brand {
    position: absolute; left: 0; top: 858px; width: 708px;
    text-align: center;
  }
  .brand-dot {
    display: block; margin: 0 auto;
    width: 34px; height: 34px; border-radius: 50%;
    background: var(--logo-grey);
  }
  .brand-name {
    display: block; margin-top: 5px;
    font-family: "Bree Serif", serif;
    font-size: 16px; letter-spacing: 1px;
    color: var(--logo-grey);
  }
</style>
</head>
<body>
<div class="canvas">
  <main class="page">
    <div class="pattern-band pattern-band--top" role="img" aria-label="Decorative band of small yellow triangles"></div>
    <div class="pattern-band pattern-band--bottom" role="img" aria-label="Decorative band of small yellow triangles"></div>
    <div class="footer-arch"></div>

    <div class="table-setting" role="img" aria-label="Illustration of a fork and knife, a plate with fish and greens, and a red checked napkin"></div>

    <section class="intro">
      <p>At Velorabix we want to help you be the best you can be!<br>
      That’s why we have put together this simple guide to motivate,<br>
      inspire, inform, and help you reach your goals.</p>
      <p>Below you will find a collection of healthy and easy recipe<br>
      ideas and tips to kickstart your detox and diet journey.</p>
    </section>

    <div class="countdown">
      <span>Ready?</span>
      <span>Set...</span>
      <span>GO!</span>
    </div>

    <footer class="brand">
      <span class="brand-dot"></span>
      <span class="brand-name">VELORABIX</span>
    </footer>
  </main>
</div>
</body>
</html>
```